Book cover design for my new Bankruptcy Law Book

Hi

I would like to get a unique and nice design for my new book titled: "Creditor Remedies Within Gulf Trade Statutes".

I like blue color. It will be in Arabic so I care the most about the design of the book cover and not the words on the cover as the printing company will handle the rest.

Much appreciated,

YUSUF BIN TAREQ

Colors
0692cd
33a6d7
86cae7
85abd2
3277b5
0255a3

Requirements
Must have
• Blue color
Nice to have
• pictures or shapes related to bankruptcy or insolvency

```html
<!DOCTYPE html>
<html lang="en">
<head>
<meta charset="utf-8">
<title>Bankruptcy Book Cover – Layout Options</title>
<link href="https://fonts.googleapis.com/css2?family=Amiri:wght@400;700&family=Lato:wght@400;700&display=swap" rel="stylesheet">
<style>
  :root {
    --page-bg: #ffffff;
    --heading-grey: #4a4a4a;
    --option-crimson: #c8104a;
    --navy-deep: #0a1540;
    --navy-mid: #142a5c;
    --navy-light: #1d3670;
    --gold-light: #ddd0a4;
    --gold-mid: #c2aa76;
    --gold-dark: #9c7d48;
    --cream-text: #f3ead2;
  }
  * { margin: 0; padding: 0; box-sizing: border-box; }
  html, body { width: 1200px; height: 1000px; overflow: hidden; background: var(--page-bg); }
  .sheet { position: relative; width: 1200px; height: 1000px; }
  .sheet-heading {
    position: absolute; top: 76px; left: 0; width: 1245px; text-align: center;
    font: 400 34px/1 "Lato", sans-serif; color: var(--heading-grey); letter-spacing: 0.5px;
  }
  .option-label {
    position: absolute; top: 170px; width: 525px; text-align: center;
    font: 400 40px/1 "Lato", sans-serif; color: var(--option-crimson); letter-spacing: 2px;
  }
  .cover {
    position: absolute; top: 242px; width: 525px; height: 679px; overflow: hidden;
    background: var(--navy-deep);
  }
  .cover--one { left: 49px; }
  .cover--two { left: 624px; }
  .pattern-zone { position: absolute; left: 0; width: 100%; }
  .chart-art {
    position: absolute;
    background: linear-gradient(135deg, rgba(194,170,118,0.32), rgba(156,125,72,0.18));
  }
  .cover-title {
    position: absolute; z-index: 2; font-family: "Amiri", serif; font-weight: 700; direction: rtl;
    background: linear-gradient(180deg, var(--gold-light), var(--gold-mid) 60%, var(--gold-dark));
    -webkit-background-clip: text; background-clip: text; color: transparent;
  }
  .cover-subtitle {
    position: absolute; z-index: 2; font-family: "Amiri", serif; font-weight: 400; direction: rtl;
    color: var(--cream-text); line-height: 1.45;
  }
  .author-band {
    position: absolute; z-index: 2; left: 0; bottom: 0; width: 100%; height: 87px;
    background: linear-gradient(90deg, var(--gold-mid), var(--gold-light) 45%, var(--gold-light) 60%, var(--gold-dark));
  }
  .author-rule {
    position: absolute; z-index: 2; left: 0; width: 100%; height: 6px;
    background: linear-gradient(90deg, var(--gold-mid), var(--gold-light), var(--gold-dark));
  }
  .author-name {
    position: absolute; left: 0; width: 100%; top: 18px; text-align: center; direction: rtl;
    font: 700 32px/1.4 "Amiri", serif; color: var(--navy-deep);
  }
  .ornament-strip {
    position: absolute; left: 0; width: 100%; height: 8px;
    background: linear-gradient(90deg, #b8923e, #e2c36a, #b8923e);
    opacity: 0.85;
  }
</style>
</head>
<body>
<main class="sheet">
  <p class="sheet-heading">Same font style but different design position &amp; arrangement</p>
  <h2 class="option-label" style="left:49px">OPTION-1</h2>
  <h2 class="option-label" style="left:650px">OPTION-2</h2>

  <section class="cover cover--one">
    <div class="pattern-zone" role="img" aria-label="Geometric star-tile pattern in navy" style="top:0;height:128px;background:linear-gradient(180deg,var(--navy-mid),var(--navy-light));"></div>
    <div class="pattern-zone" role="img" aria-label="Faint geometric star-tile pattern in deep navy" style="top:128px;height:448px;background:linear-gradient(180deg,#0f1f50,var(--navy-deep));"></div>
    <div class="chart-art" role="img" aria-label="Golden falling chart arrow cracking the ground" style="left:0;top:340px;width:330px;height:125px;"></div>
    <h1 class="cover-title" style="top:150px;left:150px;width:180px;text-align:center;font-size:76px;line-height:1.2;">إفلاس</h1>
    <p class="cover-subtitle" style="top:238px;right:50px;font-size:30px;text-align:right;">سبل انتصاف الدائنين<br>في تشريعات التجارة الخليجية</p>
    <div class="author-rule" style="top:576px;"></div>
    <div class="author-band"><p class="author-name">يوسف بن طارق</p></div>
  </section>

  <section class="cover cover--two">
    <div class="pattern-zone" role="img" aria-label="Geometric star-tile pattern in navy" style="top:0;height:108px;background:linear-gradient(180deg,var(--navy-mid),var(--navy-light));"></div>
    <div class="ornament-strip" role="img" aria-label="Gold chain ornament border" style="top:113px;"></div>
    <div class="pattern-zone" style="top:121px;height:194px;background:var(--navy-deep);"></div>
    <div class="ornament-strip" role="img" aria-label="Gold chain ornament border" style="top:315px;"></div>
    <div class="pattern-zone" role="img" aria-label="Faint geometric star-tile pattern in deep navy" style="top:323px;height:253px;background:linear-gradient(180deg,#12265a,var(--navy-deep));"></div>
    <div class="chart-art" role="img" aria-label="Golden falling chart arrow pointing down to the author band" style="left:64px;top:334px;width:452px;height:236px;"></div>
    <h1 class="cover-title" style="top:165px;left:0;width:100%;text-align:center;font-size:76px;line-height:1.2;">إفلاس</h1>
    <p class="cover-subtitle" style="top:248px;left:0;width:100%;text-align:center;font-size:27px;">سبل انتصاف الدائنين في تشريعات التجارة الخليجية</p>
    <div class="author-rule" style="top:576px;"></div>
    <div class="author-band"><p class="author-name">يوسف بن طارق</p></div>
  </section>
</main>
</body>
</html>
```